PTA Meeting Poster

We are looking to create a poster to invite parents of our school to our monthly PTA Meeting.

The copy should include:

PTA Meeting
This Wednesday
8:40am
in the Multi Purpose Room

All Welcome!

```html
<!DOCTYPE html>
<html lang="en">
<head>
<meta charset="utf-8">
<title>PTA Meeting Poster</title>
<link rel="stylesheet" href="https://fonts.googleapis.com/css2?family=Arvo:ital,wght@0,700;1,700&family=Oswald:wght@200&family=Parisienne&display=swap">
<style>
  :root {
    --page: #ffffff;
    --board: #232523;
    --board-glow: #3b4442;
    --chalk: #ffffff;
    --mint: #39d89c;
    --ink: #232523;
  }
  html, body {
    margin: 0;
    padding: 0;
    width: 1200px;
    height: 1000px;
    overflow: hidden;
    background: var(--page);
  }
  .poster {
    display: block;
    width: 1200px;
    height: 1000px;
  }
  .headline { font-family: "Arvo", "Rockwell", serif; font-weight: 700; fill: var(--chalk); }
  .day { font-family: "Parisienne", cursive; fill: var(--mint); }
  .details { font-family: "Oswald", "Arial Narrow", sans-serif; font-weight: 200; fill: var(--chalk); }
  .welcome { font-family: "Arvo", "Rockwell", serif; font-weight: 700; font-style: italic; fill: var(--ink); }
  .brace { fill: none; stroke: var(--chalk); stroke-width: 9; stroke-linejoin: round; }
  .burst-point { fill: var(--mint); }
  .band { fill: var(--mint); }
</style>
</head>
<body>
<svg class="poster" viewBox="0 0 1200 1000" xmlns="http://www.w3.org/2000/svg" role="img" aria-label="PTA Meeting this Wednesday 8:40am in the Multi Purpose Room, all welcome">
  <defs>
    <radialGradient id="board-light" cx="600" cy="480" r="420" gradientUnits="userSpaceOnUse">
      <stop offset="0" stop-color="var(--board-glow)"/>
      <stop offset="1" stop-color="var(--board)"/>
    </radialGradient>
  </defs>

  <rect class="board" x="268" y="22" width="664" height="954" fill="url(#board-light)"/>

  <g class="title-braces">
    <path class="brace" d="M327 55 C313 58 307 72 307 92 L307 186 C307 200 303 212 296 218 C303 224 307 236 307 250 L307 345 C307 365 313 378 327 381"/>
    <path class="brace" d="M873 55 C887 58 893 72 893 92 L893 186 C893 200 897 212 904 218 C897 224 893 236 893 250 L893 345 C893 365 887 378 873 381"/>
  </g>

  <text class="headline title-pta" x="600" y="273" text-anchor="middle" font-size="232" textLength="466" lengthAdjust="spacingAndGlyphs">PTA</text>
  <text class="headline title-meeting" x="600" y="367" text-anchor="middle" font-size="100" textLength="464" lengthAdjust="spacingAndGlyphs">MEETING</text>

  <text class="day" x="598" y="462" text-anchor="middle" font-size="58" transform="rotate(-7 598 462)" textLength="396" lengthAdjust="spacingAndGlyphs">This Wednesday</text>
  <text class="details time" x="852" y="544" text-anchor="end" font-size="108" textLength="134" lengthAdjust="spacingAndGlyphs">8:40am</text>
  <text class="details venue" x="615" y="648" text-anchor="middle" font-size="104" textLength="484" lengthAdjust="spacingAndGlyphs">In The MuLti Purpose Room</text>

  <g class="welcome-badge">
    <g class="burst">
      <rect class="burst-point" x="520" y="700" width="160" height="160"/>
      <rect class="burst-point" x="520" y="700" width="160" height="160" transform="rotate(15 600 780)"/>
      <rect class="burst-point" x="520" y="700" width="160" height="160" transform="rotate(30 600 780)"/>
      <rect class="burst-point" x="520" y="700" width="160" height="160" transform="rotate(45 600 780)"/>
      <rect class="burst-point" x="520" y="700" width="160" height="160" transform="rotate(60 600 780)"/>
      <rect class="burst-point" x="520" y="700" width="160" height="160" transform="rotate(75 600 780)"/>
    </g>
    <polygon class="band" points="352,790 858,706 848,818 342,905"/>
    <text class="welcome" x="600" y="830" text-anchor="middle" font-size="82" transform="rotate(-9.5 600 806)" textLength="470" lengthAdjust="spacingAndGlyphs">ALL WELCOME!</text>
  </g>
</svg>
</body>
</html>
```